Facial Cosmetic Business Card Design

I am a Physician certified in Relaxil injections, Plumatique fillers,& Chemical Peels.
I do no surgery
I have 20 years experience in facial cosmetics
30+ years medical experience
name is not TM but thought something like "Luminora Visage" catches what I do and the look I get with minimal to no downtime and no recovery time.
I do home parties and also private home consultations and treatments in a relaxed atmosphere with no pressure.
Aestheology services upon referral to a private associate as well.
I have no logo, photo's or desigs so I am ope to suggestions
Updates

To all the MD is my medical degree

the FNGHH are my board certifications stands for Fellow National Guild Household Healers
5168 Amber Hollow Lane is my office home address
4045918832 is my cell/office number or contact info

Thanks

Reason: Sorry was out of town I like a few of the designs so I have enough to choose from set tweeks to be done with prof degree and address mixup. Once i see corrections I will choose approp one thanks all Dr Whitlock

Target Market(s)

mostly wome do these procedures usually i the above 35 crowd certainly over 40 crowd for sure

Industry/Entity Type

Medical

Contact Information for Business Card

Luminora Visage, Gregory Whitlock MD, FNGHH
5168 Amber Hollow Lane
Marbury, Ga. 30571
O:470-281-9046
C:404-591-8832
F:470-281-9640

```html
<!DOCTYPE html>
<html lang="en">
<head>
<meta charset="utf-8">
<title>Luminora Visage – Business Card</title>
<link rel="stylesheet" href="https://fonts.googleapis.com/css2?family=Didact+Gothic&family=Josefin+Sans:wght@400&display=swap">
<style>
  :root {
    --stage: #e6e2dd;
    --card: #ffffff;
    --accent: #ef8a5b;
    --accent-soft: #f9d9c8;
    --ink: #4a4a4a;
    --band-text: #ffffff;
  }
  * { box-sizing: border-box; margin: 0; padding: 0; }
  html, body {
    width: 1200px; height: 900px; overflow: hidden;
    background: var(--stage);
  }
  .canvas { position: relative; width: 1200px; height: 900px; }
  .card {
    position: absolute; left: 100px; top: 164px;
    width: 1000px; height: 572px;
    background: var(--card);
    box-shadow: 0 6px 18px rgba(0,0,0,0.18);
    overflow: hidden;
  }
  .card__band {
    position: absolute; left: 0; top: 0; width: 100%; height: 124px;
    background: var(--accent);
    color: var(--band-text);
    font-family: "Didact Gothic", sans-serif;
    font-size: 25px; line-height: 32px; letter-spacing: 0.5px;
    text-align: center;
    padding-top: 14px;
  }
  .card__profile-art {
    position: absolute; left: 50px; top: 150px; width: 110px; height: 390px;
    background: linear-gradient(160deg, var(--accent-soft), #fff 85%);
    border-radius: 60px 16px 30px 70px;
  }
  .brand {
    position: absolute; left: 180px; top: 255px;
    font-family: "Didact Gothic", sans-serif;
    font-weight: 400;
    font-size: 60px; line-height: 72px; letter-spacing: 2px;
    color: var(--ink);
  }
  .contacts {
    position: absolute; left: 640px; top: 160px;
    list-style: none;
    font-family: "Didact Gothic", sans-serif;
    font-size: 29px; color: var(--accent);
  }
  .contacts li { display: flex; align-items: center; height: 40px; }
  .contacts svg { width: 22px; height: 22px; margin-right: 14px; fill: var(--ink); }
  .owner {
    position: absolute; left: 290px; top: 430px;
    font-family: "Josefin Sans", sans-serif;
    color: var(--ink);
    font-size: 42px; line-height: 50px; letter-spacing: 2px; text-transform: uppercase;
    white-space: nowrap;
  }
  .owner__credentials { font-size: 26px; letter-spacing: 1px; margin-left: 10px; }
</style>
</head>
<body>
<main class="canvas">
  <article class="card">
    <header class="card__band">
      <p>20 years experience in facial cosmetics</p>
      <p>30+ years medical experience</p>
      <p>Available for home parties and private home consultations</p>
    </header>

    <div class="card__profile-art" role="img" aria-label="Line illustration of a woman's profile in orange"></div>

    <h1 class="brand">Luminora Visage</h1>

    <ul class="contacts">
      <li>
        <svg viewBox="0 0 24 24" aria-hidden="true"><path d="M6.6 10.8a15 15 0 0 0 6.6 6.6l2.2-2.2c.3-.3.7-.4 1-.2 1.1.4 2.3.6 3.6.6.6 0 1 .4 1 1V20c0 .6-.4 1-1 1A17 17 0 0 1 3 4c0-.6.4-1 1-1h3.5c.6 0 1 .4 1 1 0 1.3.2 2.5.6 3.6.1.3 0 .7-.2 1z"/></svg>
        470-281-9046
      </li>
      <li>
        <svg viewBox="0 0 24 24" aria-hidden="true"><path d="M7 2h10a1 1 0 0 1 1 1v18a1 1 0 0 1-1 1H7a1 1 0 0 1-1-1V3a1 1 0 0 1 1-1zm1 3v12h8V5zm4 13.5a1 1 0 1 0 0 2 1 1 0 0 0 0-2z"/></svg>
        404-591-8832
      </li>
      <li>
        <svg viewBox="0 0 24 24" aria-hidden="true"><path d="M4 8h3V3h10v5h3a1 1 0 0 1 1 1v11H3V9a1 1 0 0 1 1-1zm5-3v3h6V5zm-3 7v2h12v-2zm0 4v2h12v-2z"/></svg>
        470-281-9640
      </li>
    </ul>

    <p class="owner">Gregory Whitlock<span class="owner__credentials">MD. FNGHH</span></p>
  </article>
</main>
</body>
</html>
```